Construction Company

Design a clutter free business card, it can be double-sided utilizing the logo for VKM Ltd simple with all relevant contact information.

Please also a letterhead design to function for the purposes of invoicing, all mail requirements, with header to be distinctive while the footer ties page together and incorporates all necessary information.

For now, please use generic / dummy text and when a winner is selected, I will disclose the contact information.

Hi Designers! Please read the updated brief which includes the design of a business card and letterhead. Thank you!

```html
<!DOCTYPE html>
<html lang="en">
<head>
<meta charset="utf-8">
<title>VKM Ltd — Business Card</title>
<link rel="stylesheet" href="https://fonts.googleapis.com/css2?family=Montserrat:wght@400;500;600;700&family=Playfair+Display:wght@500&display=swap">
<style>
  :root {
    --royal-blue: #0a3399;
    --deep-blue: #0b2f8f;
    --gold: #b8901c;
    --paper: #ffffff;
    --ink: #2b2b2b;
    --backdrop: #e9e9ec;
  }
  * { box-sizing: border-box; margin: 0; padding: 0; }
  html, body { width: 1200px; height: 930px; overflow: hidden; }
  body {
    background: var(--backdrop);
    font-family: "Montserrat", Arial, sans-serif;
    position: relative;
  }
  .card {
    position: absolute;
    left: 250px;
    width: 700px;
    height: 400px;
    border-radius: 26px;
    overflow: hidden;
    box-shadow: 0 10px 30px rgba(0,0,0,0.18);
  }
  .card-front {
    top: 45px;
    background: linear-gradient(135deg, #1a45b0 0%, var(--royal-blue) 55%, var(--deep-blue) 100%);
    display: flex;
    align-items: center;
    justify-content: center;
  }
  .brand {
    display: flex;
    align-items: center;
    gap: 14px;
    font-family: "Playfair Display", Georgia, serif;
    font-weight: 500;
    white-space: nowrap;
  }
  .brand-dot { border-radius: 50%; flex: none; }
  .card-front .brand { color: var(--paper); font-size: 78px; }
  .card-front .brand-dot { width: 30px; height: 30px; background: var(--gold); }

  .card-back { top: 485px; background: var(--paper); }
  .card-back .wave { position: absolute; left: 0; top: 0; width: 700px; height: 400px; }
  .card-back .brand {
    position: absolute; left: 44px; top: 168px;
    color: var(--royal-blue); font-size: 50px; gap: 10px;
  }
  .card-back .brand-dot { width: 20px; height: 20px; background: var(--gold); }

  .holder { position: absolute; right: 42px; top: 170px; text-align: right; }
  .holder-name { color: var(--royal-blue); font-weight: 700; font-size: 22px; letter-spacing: 0.5px; }
  .holder-role { color: var(--ink); font-size: 14px; margin-top: 2px; }
  .gold-tab { position: absolute; right: 0; top: 166px; width: 10px; height: 34px; background: var(--gold); }
  .divider { position: absolute; left: 44px; right: 30px; top: 258px; height: 1.5px; background: var(--royal-blue); }

  .contacts { position: absolute; left: 44px; top: 282px; list-style: none; }
  .contacts li {
    display: flex; align-items: center; gap: 10px;
    color: var(--ink); font-size: 16px; line-height: 26px;
  }
  .contacts svg { width: 13px; height: 13px; flex: none; }
  .address {
    position: absolute; right: 42px; top: 282px; text-align: right;
    color: var(--ink); font-size: 15px; line-height: 22px;
  }
</style>
</head>
<body>
  <section class="card card-front" aria-label="Business card front">
    <div class="brand"><span class="brand-dot"></span><span class="brand-name">VKM Ltd</span></div>
  </section>

  <section class="card card-back" aria-label="Business card back">
    <svg class="wave" viewBox="0 0 700 400" aria-hidden="true">
      <path d="M0 0 H700 V40 C560 80 360 90 220 120 C120 140 40 160 0 175 Z" fill="var(--royal-blue)"/>
      <path d="M0 175 C40 160 120 140 220 120 C360 90 560 80 700 40 V58 C560 98 360 108 225 136 C125 156 45 176 0 192 Z" fill="var(--gold)"/>
      <path d="M0 200 C45 184 125 164 225 144 C200 152 60 190 0 212 Z" fill="var(--royal-blue)"/>
    </svg>

    <div class="brand"><span class="brand-dot"></span><span class="brand-name">VKM Ltd</span></div>

    <div class="holder">
      <p class="holder-name">DANIEL REEVE</p>
      <p class="holder-role">Founder</p>
    </div>
    <span class="gold-tab"></span>
    <span class="divider"></span>

    <ul class="contacts">
      <li>
        <svg viewBox="0 0 24 24"><path fill="var(--royal-blue)" d="M6.6 10.8a15 15 0 0 0 6.6 6.6l2.2-2.2a1 1 0 0 1 1-.25 11.4 11.4 0 0 0 3.6.57 1 1 0 0 1 1 1V20a1 1 0 0 1-1 1A17 17 0 0 1 3 4a1 1 0 0 1 1-1h3.5a1 1 0 0 1 1 1c0 1.25.2 2.45.57 3.57a1 1 0 0 1-.25 1z"/></svg>
        (555) 214-7730
      </li>
      <li>
        <svg viewBox="0 0 24 24"><rect x="2.5" y="5" width="19" height="14" rx="1.5" fill="none" stroke="var(--royal-blue)" stroke-width="2.4"/><path d="M3 6l9 7 9-7" fill="none" stroke="var(--royal-blue)" stroke-width="2.4"/></svg>
        info@vkmltd.com
      </li>
      <li>
        <svg viewBox="0 0 24 24"><circle cx="12" cy="12" r="9.5" fill="none" stroke="var(--royal-blue)" stroke-width="2.2"/><path d="M2.5 12h19M12 2.5c3 3 3 16 0 19M12 2.5c-3 3-3 16 0 19" fill="none" stroke="var(--royal-blue)" stroke-width="1.8"/></svg>
        www.vkmltd.com
      </li>
    </ul>

    <p class="address">718 Harbor Lane<br>Fairview, DE 19700</p>
  </section>
</body>
</html>
```